fernwick study hub community

The website presents a new interactive learning system where it provides not only the teaching material as the instructor friend who can both teach and learn, making friends and making money.
Make friends and get money.

```html
<!DOCTYPE html>
<html lang="en">
<head>
<meta charset="utf-8">
<title>fernwick study hub community</title>
<link href="https://fonts.googleapis.com/css2?family=Lato:wght@300;400;700&display=swap" rel="stylesheet">
<style>
:root{
  --topbar:#2b3a4d;
  --topline:#3a6fd1;
  --ink:#1d2a44;
  --hero:#363e40;
  --blue:#1c5fcc;
  --blue-dark:#143f92;
  --btn-edge:#123a8a;
  --about:#1b3b5c;
  --footer:#2a2a2a;
  --white:#ffffff;
}
*{box-sizing:border-box;margin:0;padding:0}
html,body{width:1200px;height:2261px;overflow:hidden}
body{position:relative;font-family:'Lato',sans-serif;color:var(--ink);background:var(--white)}

.topbar{position:absolute;left:0;top:0;width:1200px;height:48px;background:var(--topbar);border-top:4px solid var(--topline);color:var(--white);font-size:12px;font-weight:700}
.topbar .cell{position:absolute;top:0;height:44px;display:flex;align-items:center;border-left:1px solid #3f4e62}
.lang{left:125px;width:162px;padding-left:16px}
.lang .flag{width:14px;height:9px;background:#c8cfe0;margin-right:10px}
.lang .caret{position:absolute;right:14px;top:17px;width:7px;height:7px;border-right:1.5px solid #cfd6e2;border-bottom:1.5px solid #cfd6e2;transform:rotate(45deg)}
.phone{left:287px;width:420px;padding-left:14px;font-weight:400;font-size:13px}
.phone svg{margin-right:6px}
.account{left:707px;width:157px;justify-content:center;gap:7px;font-size:11px}
.account .or{font-weight:400}
.account .join{background:var(--white);color:var(--ink);padding:3px 9px;border-radius:2px}
.search{left:864px;width:211px;padding-left:14px;font-weight:400;font-size:12px;color:#d5dbe5;border-right:1px solid #3f4e62}
.search svg{position:absolute;right:14px;top:15px}

.nav{position:absolute;left:0;top:48px;width:1200px;height:90px;background:var(--white);border-bottom:2px solid #7f868c}
.brand{position:absolute;left:125px;top:27px;display:flex;align-items:center;gap:12px;font-size:22px;font-weight:700;color:var(--ink)}
.brand .mark{width:34px;height:34px;border-radius:50%;background:var(--ink)}
.menu{position:absolute;right:125px;top:34px;display:flex;gap:38px;list-style:none;font-size:15px;color:var(--ink)}

.hero{position:absolute;left:0;top:138px;width:1200px;height:498px;background:var(--hero);overflow:hidden}
.hero .photo{position:absolute;left:640px;top:51px;width:436px;height:447px;z-index:1;background:linear-gradient(160deg,#6b6f70 0%,#c9a79a 45%,#e9e9ea 100%)}
.hero h1{position:absolute;left:130px;top:108px;z-index:2;white-space:nowrap;color:var(--white);font-size:42px;line-height:61px;font-weight:700;letter-spacing:-.3px}
.hero p{position:absolute;left:133px;top:245px;width:470px;z-index:2;color:var(--white);font-size:21px;line-height:31px}
.hero .cta{position:absolute;left:133px;top:330px;width:195px;height:48px;z-index:2;background:var(--blue);border-bottom:5px solid var(--btn-edge);color:var(--white);font-size:15px;font-weight:700;display:flex;align-items:center;justify-content:center}

.section-head{position:absolute;left:0;width:1200px;text-align:center}
.section-head .icon{width:52px;height:52px;margin:0 auto;border-radius:50%}
.section-head h2{font-size:36px;font-weight:400;line-height:44px;margin-top:4px}
.section-head p{width:560px;margin:6px auto 0;font-size:15px;line-height:24px}
.works-head{top:657px;color:var(--ink)}
.works-head .icon{background:var(--ink)}

.step{position:absolute;height:188px}
.step.right{z-index:2}
.step .num{position:absolute;top:0;width:151px;height:188px;background:var(--blue);clip-path:polygon(0 0,100% 0,100% 74%,50% 100%,0 74%);color:var(--white);font-size:62px;font-weight:300;display:flex;justify-content:center;padding-top:34px;filter:drop-shadow(0 2px 3px rgba(0,0,0,.3))}
.step .panel{position:absolute;top:0;width:285px;height:140px;background:var(--blue-dark);color:var(--white);padding:16px 20px 0 30px;box-shadow:2px 3px 6px rgba(0,0,0,.35)}
.step h3{font-size:21px;font-weight:400;line-height:28px;margin-bottom:6px}
.step .panel p{font-size:12px;line-height:18px;width:215px}
.step.left .num{left:0}
.step.left .panel{left:151px}
.step.right .panel{left:0;padding-left:34px}
.step.right .num{left:285px}

.about{position:absolute;left:0;top:1621px;width:1200px;height:562px;background:var(--about);color:var(--white)}
.about-head{top:26px;color:var(--white)}
.about-head .icon{background:var(--white)}
.about .copy{position:absolute;left:127px;top:240px;width:480px;font-size:12.5px;line-height:25px}
.about .copy p+p{margin-top:12px}
.about .visual{position:absolute;left:647px;top:219px;width:427px;height:309px;background:radial-gradient(circle at 50% 55%,#2f8fe6 0%,#1553a8 55%,#0b2a55 100%);box-shadow:0 3px 8px rgba(0,0,0,.4)}

.footer{position:absolute;left:0;top:2183px;width:1200px;height:78px;background:var(--footer);color:var(--white)}
.connect{position:absolute;left:148px;top:27px;display:flex;align-items:center;gap:6px;font-size:17px}
.connect span{margin-right:6px}
.connect i{display:block;width:19px;height:19px;background:var(--white);border-radius:3px}
.copyright{position:absolute;right:126px;top:30px;font-size:13px}
</style>
</head>
<body>

<header class="topbar">
  <div class="cell lang"><span class="flag"></span>English<span class="caret"></span></div>
  <div class="cell phone">
    <svg width="11" height="11" viewBox="0 0 24 24"><path fill="#fff" d="M6.6 10.8a15.1 15.1 0 0 0 6.6 6.6l2.2-2.2c.3-.3.7-.4 1-.2 1.1.4 2.3.6 3.6.6.6 0 1 .4 1 1V20c0 .6-.4 1-1 1A17 17 0 0 1 3 4c0-.6.4-1 1-1h3.5c.6 0 1 .4 1 1 0 1.3.2 2.5.6 3.6.1.3 0 .7-.2 1z"/></svg>
    +2190004172
  </div>
  <div class="cell account"><span>Sign in</span><span class="or">or</span><span class="join">Join now</span></div>
  <div class="cell search">Search...
    <svg width="13" height="13" viewBox="0 0 24 24"><circle cx="10" cy="10" r="7" fill="none" stroke="#fff" stroke-width="3"/><line x1="15" y1="15" x2="22" y2="22" stroke="#fff" stroke-width="3"/></svg>
  </div>
</header>

<nav class="nav">
  <div class="brand"><span class="mark"></span>fernwick study hub</div>
  <ul class="menu">
    <li>Home</li><li>About Us</li><li>Make friends</li><li>How it Works</li><li>Service</li><li>Contact</li>
  </ul>
</nav>

<section class="hero">
  <div class="photo" role="img" aria-label="Photo of a smiling student holding an open laptop"></div>
  <h1>BY MAKING FRIENDS<br>YOU CAN MAKE MONEY</h1>
  <p>It is a long established fact that a reader will be distracted by the readable content of a page whe</p>
  <div class="cta">GET STARTED NOW</div>
</section>

<div class="section-head works-head">
  <div class="icon"></div>
  <h2>How it works</h2>
  <p>It is a long established fact that a reader will be distracted by the readable content of a page when looking at its layout.</p>
</div>

<div class="step left" style="left:184px;top:840px">
  <div class="num">01</div>
  <div class="panel"><h3>Drops</h3><p>It is a long established fact that a reader will be distracted by the read-able content of a page when looking at</p></div>
</div>
<div class="step right" style="left:579px;top:950px">
  <div class="panel"><h3>Report Your Finding</h3><p>It is a long established fact that a reader will be distracted by the read-able content of a page when looking at</p></div>
  <div class="num">02</div>
</div>
<div class="step left" style="left:186px;top:1064px">
  <div class="num">03</div>
  <div class="panel"><h3>Be a Friend Instructor</h3><p>It is a long established fact that a reader will be distracted by the read-able content of a page when looking at</p></div>
</div>
<div class="step right" style="left:579px;top:1185px">
  <div class="panel"><h3>Give your Suggetions</h3><p>It is a long established fact that a reader will be distracted by the read-able content of a page when looking at</p></div>
  <div class="num">04</div>
</div>
<div class="step left" style="left:188px;top:1281px">
  <div class="num">05</div>
  <div class="panel"><h3>Create Your Goute</h3><p>It is a long established fact that a reader will be distracted by the read-able content of a page when looking at</p></div>
</div>
<div class="step right" style="left:580px;top:1392px">
  <div class="panel"><h3>FSH News</h3><p>It is a long established fact that a reader will be distracted by the read-able content of a page when looking at</p></div>
  <div class="num">06</div>
</div>

<section class="about">
  <div class="section-head about-head">
    <div class="icon"></div>
    <h2>About us</h2>
    <p>It is a long established fact that a reader will be distracted by the readable content of a page when looking at its layout.</p>
  </div>
  <div class="copy">
    <p>It is a long established fact that a reader will be distracted by the readable content of a page when looking at its layout. The point of using Lorem Ipsum is that it has a more-or-less normal distribution of letters, as opposed to using 'Content here, content here', making it look like readable English. Many desktop publishing packages</p>
    <p>There are many variations of passages of Lorem Ipsum available, but the majority have suffered alteration in some form, by injected humour, or randomised words which don't<br>Contrary to popular belief, Lorem Ipsum is not simply random text. It has roots in a piece of classical Latin literature from 45 BC, making it over 2000 years old. Harold Penwick</p>
  </div>
  <div class="visual" role="img" aria-label="Illustration of a light bulb drawing a cloud raining drops on a blue grid"></div>
</section>

<footer class="footer">
  <div class="connect"><span>Connect with Us :</span><i></i><i></i><i></i><i></i></div>
  <div class="copyright">@2014-2015 fernwick study hub All Copy Right</div>
</footer>

</body>
</html>
```